Business Card for Vorla Parts Wholesale supplier

Hi There! I need a new business card for our company. We are specialized in selling Vorla parts, mostly we sell new LCD screens for Zelnar and Drelks. I would like to see that back in the design.

You can find the colors and logo's on our website: www.hartuvo.nl

Industry/Entity Type

Business

Contact Information for Business Card

My Details:
Tobias Lindqvist

Phone: 0031687203316
E-mail: Tobias@hartuvo.nl

Slogan: "Because Quality Matters"

Font styles to use
Sans Serif

Colors

Designer to choose colors to be used in the design.

Requirements
Must have
• A Black backside with the Hartuvo logo on it. The front side should be clean with only my contact details.
• But I'm also open for something really different or awesome!
Nice to have
• Remember that we are in the parts & repairing industry, So i'll be handing those business cards mainly to repair companies. Maybe you can do something with that thought :)

```html
<!DOCTYPE html>
<html lang="en">
<head>
<meta charset="utf-8">
<title>Hartuvo Business Card</title>
<link href="https://fonts.googleapis.com/css2?family=Roboto:wght@400;500;700&display=swap" rel="stylesheet">
<style>
  :root {
    --canvas-bg: #e6e6e6;
    --card-dark: #1f1f1f;
    --card-dark-deep: #121212;
    --card-dark-light: #2c2c2c;
    --card-light: #f7f7f7;
    --accent: #ec6a1e;
    --ink: #1c1c1c;
    --ink-soft: #333333;
    --white: #ffffff;
  }
  * { box-sizing: border-box; margin: 0; padding: 0; }
  html, body {
    width: 1200px;
    height: 576px;
    overflow: hidden;
    background: var(--canvas-bg);
    font-family: "Roboto", Arial, sans-serif;
  }
  .stage { position: relative; width: 1200px; height: 576px; }

  .card {
    position: absolute;
    top: 138px;
    width: 484px;
    height: 294px;
    border-radius: 14px;
    overflow: hidden;
    box-shadow: 0 3px 8px rgba(0,0,0,0.25);
  }

  /* Back side */
  .card-back { left: 82px; background: var(--card-dark); }
  .card-back .backdrop {
    position: absolute; inset: 0;
    background:
      radial-gradient(ellipse at 60% 35%, var(--card-dark-light) 0%, transparent 55%),
      linear-gradient(160deg, var(--card-dark-deep) 0%, var(--card-dark) 45%, var(--card-dark) 100%);
  }
  .card-back .brand {
    position: absolute;
    left: 104px; top: 116px;
    display: flex; align-items: center; gap: 14px;
  }
  .card-back .brand-mark {
    width: 50px; height: 50px; border-radius: 50%;
    background: var(--accent);
  }
  .card-back .brand-name {
    font-weight: 500; font-size: 50px; line-height: 1;
    color: var(--white); letter-spacing: 0.5px;
  }

  /* Front side */
  .card-front { left: 602px; width: 481px; background: var(--card-light); }
  .card-front .brand {
    position: absolute; left: 50px; top: 118px;
    display: flex; align-items: center; gap: 11px;
  }
  .card-front .brand-mark {
    width: 52px; height: 52px; border-radius: 50%;
    background: var(--accent);
  }
  .card-front .brand-name {
    font-weight: 500; font-size: 38px; line-height: 1;
    color: var(--ink); letter-spacing: 0.3px;
  }
  .card-front .slogan {
    position: absolute; left: 113px; top: 159px;
    font-size: 13.5px; color: var(--ink-soft);
  }

  .contact { position: absolute; left: 305px; top: 91px; }
  .contact-name {
    font-weight: 700; font-size: 18px; color: var(--accent);
  }
  .contact-role {
    font-size: 11px; color: var(--ink); margin-top: 3px;
  }
  .contact-list { list-style: none; margin-top: 20px; }
  .contact-list li {
    display: flex; align-items: center; gap: 12px;
    font-size: 12px; color: var(--ink); height: 16.5px;
  }
  .contact-list svg { width: 12px; height: 12px; fill: var(--accent); flex: none; }
</style>
</head>
<body>
<main class="stage">
  <section class="card card-back">
    <div class="backdrop" role="img" aria-label="Dark close-up photo of a phone with a cracked screen"></div>
    <div class="brand">
      <span class="brand-mark"></span>
      <span class="brand-name">hartuvo</span>
    </div>
  </section>

  <section class="card card-front">
    <div class="brand">
      <span class="brand-mark"></span>
      <span class="brand-name">hartuvo</span>
    </div>
    <p class="slogan">Because Quality Matters</p>

    <div class="contact">
      <p class="contact-name">Tobias Lindqvist</p>
      <p class="contact-role">Managing Director</p>
      <ul class="contact-list">
        <li>
          <svg viewBox="0 0 12 12" aria-hidden="true"><path d="M1 4 Q6 0 11 4 L9.5 5.5 L8 4.5 L4 4.5 L2.5 5.5 Z M3 6 H9 L10.5 11 H1.5 Z"/></svg>
          0031687203316
        </li>
        <li>
          <svg viewBox="0 0 12 12" aria-hidden="true"><path d="M6 0.5a5.5 5.5 0 1 0 0 11a5.5 5.5 0 1 0 0-11Zm0 1c.7.8 1.2 2 1.4 3.5H4.6C4.8 3.5 5.3 2.3 6 1.5Zm-1.6.3c-.5.9-.8 2-.9 3.2H1.6a4.5 4.5 0 0 1 2.8-3.2Zm3.2 0a4.5 4.5 0 0 1 2.8 3.2H8.5c-.1-1.2-.4-2.3-.9-3.2ZM1.6 6h1.9c.1 1.2.4 2.3.9 3.2A4.5 4.5 0 0 1 1.6 6Zm3 0h2.8c-.2 1.5-.7 2.7-1.4 3.5C5.3 8.7 4.8 7.5 4.6 6Zm3.9 0h1.9a4.5 4.5 0 0 1-2.8 3.2c.5-.9.8-2 .9-3.2Z"/></svg>
          Tobias@hartuvo.nl
        </li>
        <li>
          <svg viewBox="0 0 12 12" aria-hidden="true"><path d="M0.5 2.5H11.5V9.5H0.5Z M1.2 3 L6 6.6 L10.8 3" stroke="#f7f7f7" stroke-width="0.8"/></svg>
          www.hartuvo.nl
        </li>
      </ul>
    </div>
  </section>
</main>
</body>
</html>
```